New Alcoholic Spiked Seltzer Line

We need a can design for a line of low calorie alcoholic seltzer. This product is a sparkling water and vodka drink with no sugar added in a slim 12 oz can.

This is a lighter, healthier, alternative to the sugary ready-to-drinks on the market. The product contains only 3 ingredients: Vodka, Water and Natural Flavors. It has only 100 calories but still has 5% alcohol, so you don't need to sacrifice alcohol to cut calories.

This product also does not contain any preservatives.

We want this design to communicate the following objectives to the consumer and in this order:

1. Appetizing product
2.Low calorie
3.Communicate the type of beverage (Spiked Seltzer)

The brand name of the product is VELKA.

The flavor of the product needed to be used for the design is Mango-Orange.

Comparable products are:

www.brindlefizzworks.example/
https://www.quorvabubbles.example
https://pelnavo.example/

The designs should not infringe or copy the creative directions of the products mentionned above. They are only given so that you can better understand the type of product we are developing.

Target Market(s)

Young Professional women between the ages of 25 and 44

Industry/Entity Type

Product

Colors

Designer to choose colors to be used in the design.

Requirements
Must have
• Design extendibility, meaning it can be adapted for other flavors.
• This is a new category in the market we are targeting, so consumers must easily be able to identify what type of product this is.

```html
<!DOCTYPE html>
<html lang="en">
<head>
<meta charset="utf-8">
<title>VELKA Spiked Seltzer – Mango Orange Can Label</title>
<link rel="stylesheet" href="https://fonts.googleapis.com/css2?family=Open+Sans:wght@400;600&family=Kaushan+Script&display=swap">
<style>
  :root {
    --silver-light: #f1f2f3;
    --silver-mid: #d3d5d7;
    --silver-dark: #a9acaf;
    --wine: #7a1016;
    --crimson: #c8203a;
    --berry-bar: #b01f48;
    --ink-grey: #4a4a4a;
    --brand-ink: #2e2e30;
    --mango: #f2a20f;
    --mango-deep: #e58f05;
    --band-black: #262627;
    --band-text: #f5a623;
    --white: #ffffff;
  }
  html, body {
    margin: 0;
    padding: 0;
    width: 1200px;
    height: 2546px;
    overflow: hidden;
  }
  .label {
    position: relative;
    width: 1200px;
    height: 2546px;
    overflow: hidden;
    background: linear-gradient(90deg,
      var(--silver-dark) 0%,
      var(--silver-mid) 12%,
      var(--silver-light) 38%,
      var(--silver-mid) 70%,
      var(--silver-dark) 100%);
    font-family: "Open Sans", Arial, sans-serif;
  }
  .product-copy {
    position: absolute;
    left: 0;
    width: 530px;
    margin: 0;
    text-align: right;
  }
  .category {
    top: 490px;
    color: var(--wine);
    font-weight: 400;
    font-size: 92px;
    line-height: 96px;
  }
  .tagline {
    top: 700px;
    color: var(--crimson);
    font-size: 46px;
    line-height: 52px;
  }
  .ingredients {
    top: 808px;
    color: var(--ink-grey);
    font-size: 50px;
    line-height: 56px;
  }
  .accent-bar {
    position: absolute;
    left: 140px;
    top: 966px;
    width: 392px;
    height: 52px;
    background: var(--berry-bar);
  }
  .brand-name {
    position: absolute;
    left: 580px;
    top: 1100px;
    width: 560px;
    margin: 0;
    text-align: center;
    color: var(--brand-ink);
    font-family: "Open Sans", Arial, sans-serif;
    font-weight: 600;
    font-size: 150px;
    line-height: 180px;
  }
  .flavor-badge {
    position: absolute;
    left: 20px;
    top: 1440px;
    width: 510px;
    height: 510px;
    border-radius: 50%;
    background: radial-gradient(circle at 40% 35%, var(--mango) 0%, var(--mango-deep) 100%);
    display: flex;
    flex-direction: column;
    align-items: center;
    justify-content: center;
    transform: rotate(-12deg);
  }
  .flavor-badge span {
    font-family: "Kaushan Script", cursive;
    color: var(--white);
    font-size: 108px;
    line-height: 110px;
  }
  .flavor-badge .flavor-second { margin-left: 40px; }
  .stats-band {
    position: absolute;
    left: 0;
    bottom: 0;
    width: 1200px;
    height: 410px;
    background: var(--band-black);
  }
  .stats-band p {
    margin: 0;
    padding-top: 72px;
    text-align: center;
    color: var(--band-text);
    font-size: 58px;
    letter-spacing: 1px;
  }
</style>
</head>
<body>
  <main class="label">
    <h1 class="product-copy category">Spiked<br>Seltzer</h1>
    <p class="product-copy tagline">low calorie<br>alcoholic seltzer</p>
    <p class="product-copy ingredients">vodka, water &amp;<br>natural flavors</p>
    <div class="accent-bar"></div>

    <p class="brand-name">VELKA</p>

    <div class="flavor-badge">
      <span class="flavor-first">mango</span>
      <span class="flavor-second">orange</span>
    </div>

    <footer class="stats-band">
      <p>5% alcohol - 100 calories</p>
    </footer>
  </main>
</body>
</html>
```